Lakeshore Claims Adjusters Business card

We need to get business card Design for our Company we are Public Adjusters in Chicago Illinois - i like to see good combination and elements from my Company Logo. as well To be an two side design
Updates

Target Market(s)

Home /Business owner Property Managers

Industry/Entity Type

Business

Contact Information for Business Card

to show the Element of our logo i will Like 3D

Font styles to use
Sans Serif

Requirements
Must have
• Logo and Element of the Logo in 3D
Nice to have
• Logo That we Provide 3D Same Colors or open for suggestions
Should not have
• unleare view -

```html
<!DOCTYPE html>
<html lang="en">
<head>
<meta charset="utf-8">
<title>Lakeshore Claims Adjusters — Business Card</title>
<link href="https://fonts.googleapis.com/css2?family=Open+Sans:wght@400;600&display=swap" rel="stylesheet">
<style>
  :root {
    --page: #e9e6e1;
    --card-white: #ffffff;
    --brand-red: #cc0000;
    --brand-blue: #1a2fb0;
    --text-grey: #555555;
    --rule-grey: #d5d5d5;
  }
  html, body {
    margin: 0;
    padding: 0;
    width: 1200px;
    height: 987px;
    overflow: hidden;
    background: var(--page);
    font-family: "Open Sans", sans-serif;
  }
  .canvas {
    position: relative;
    width: 1200px;
    height: 987px;
  }
  .card {
    position: absolute;
    left: 293px;
    width: 615px;
    height: 352px;
    overflow: hidden;
    box-shadow: 0 2px 6px rgba(0,0,0,0.25);
  }
  /* Front */
  .card-front {
    top: 130px;
    background: var(--card-white);
  }
  .brand-block {
    position: absolute;
    left: 20px;
    top: 0;
    width: 300px;
    height: 329px;
    display: flex;
    flex-direction: column;
    align-items: center;
    justify-content: center;
    gap: 14px;
  }
  .brand-mark {
    width: 46px;
    height: 46px;
    border-radius: 50%;
    background: var(--brand-blue);
  }
  .brand-name {
    font-weight: 600;
    font-size: 19px;
    color: var(--brand-blue);
    text-align: center;
    line-height: 1.25;
  }
  .divider {
    position: absolute;
    left: 320px;
    top: 57px;
    width: 1px;
    height: 234px;
    background: var(--rule-grey);
  }
  .contact {
    position: absolute;
    left: 355px;
    top: 58px;
    color: var(--text-grey);
  }
  .contact-name {
    margin: 0;
    font-weight: 600;
    font-size: 22px;
    line-height: 1.2;
    color: var(--brand-blue);
    letter-spacing: 0.3px;
  }
  .contact-title {
    margin: 0 0 10px;
    font-size: 16.5px;
    line-height: 1.3;
    color: var(--brand-red);
  }
  .contact-address {
    margin: 0 0 5px;
    font-size: 16px;
    line-height: 23px;
  }
  .contact-list {
    list-style: none;
    margin: 0;
    padding: 0;
    font-size: 16px;
    line-height: 23.4px;
  }
  .contact-list li {
    display: flex;
    align-items: center;
    gap: 8px;
  }
  .contact-list svg {
    width: 15px;
    height: 15px;
    fill: var(--brand-blue);
    flex: none;
  }
  .front-band {
    position: absolute;
    left: 0;
    bottom: 0;
    width: 615px;
    height: 23px;
  }
  /* Back */
  .card-back {
    top: 506px;
    background: var(--brand-red);
  }
  .back-brand {
    position: absolute;
    left: 0;
    top: 110px;
    width: 615px;
    display: flex;
    flex-direction: column;
    align-items: center;
    gap: 16px;
  }
  .back-brand .brand-mark {
    width: 64px;
    height: 64px;
    background: var(--brand-blue);
  }
  .back-brand .brand-name {
    color: var(--card-white);
    font-size: 24px;
  }
  .back-rule {
    position: absolute;
    left: 95px;
    top: 270px;
    width: 425px;
    height: 1px;
    background: linear-gradient(90deg, transparent, var(--brand-blue), transparent);
  }
  .back-url {
    position: absolute;
    left: 0;
    top: 282px;
    width: 615px;
    text-align: center;
    color: var(--card-white);
    font-size: 16px;
    letter-spacing: 2.2px;
  }
</style>
</head>
<body>
<main class="canvas">

  <section class="card card-front" aria-label="Business card front">
    <div class="brand-block">
      <span class="brand-mark" aria-hidden="true"></span>
      <div class="brand-name">Lakeshore Claims Adjusters</div>
    </div>

    <div class="divider"></div>

    <div class="contact">
      <h1 class="contact-name">MARCUS DELANEY</h1>
      <p class="contact-title">CEO/Founder</p>
      <p class="contact-address">2140 Larkspur Court<br>Evanston, Illinois 60201</p>
      <ul class="contact-list">
        <li>
          <svg viewBox="0 0 16 16" aria-hidden="true"><path d="M3.6 1.2l2.3 2.9-1.2 1.6c.9 2 2.6 3.7 4.6 4.6l1.6-1.2 2.9 2.3-1.4 2.6C7 13.5 2.5 9 1 3l2.6-1.8z"/></svg>
          312 555 0148
        </li>
        <li>
          <svg viewBox="0 0 16 16" aria-hidden="true"><path d="M4.5 0.5h7a1 1 0 0 1 1 1v13a1 1 0 0 1-1 1h-7a1 1 0 0 1-1-1v-13a1 1 0 0 1 1-1zm.7 2v10h5.6v-10z M7.3 13.2h1.4v1.2H7.3z"/></svg>
          312 555 0172
        </li>
        <li>
          <svg viewBox="0 0 16 16" aria-hidden="true"><path d="M4 1h6l2 2v3H4z M1 7h14v6H1z M3 14h10v1.5H3z"/></svg>
          312 555 0190
        </li>
        <li>
          <svg viewBox="0 0 16 16" aria-hidden="true"><path d="M1 3h14v10H1z M2 4l6 5 6-5" fill="none" stroke="#1a2fb0" stroke-width="1.6"/></svg>
          info@lakeshoreclaims.com
        </li>
        <li>
          <svg viewBox="0 0 16 16" aria-hidden="true"><circle cx="8" cy="8" r="7"/><path d="M1.5 8h13M8 1c-3 3.5-3 10.5 0 14M8 1c3 3.5 3 10.5 0 14" fill="none" stroke="#fff" stroke-width="1"/></svg>
          www.lakeshoreclaims.com
        </li>
      </ul>
    </div>

    <svg class="front-band" viewBox="0 0 615 23" preserveAspectRatio="none" aria-hidden="true">
      <defs>
        <linearGradient id="bandBlue" x1="0" x2="1" y1="0" y2="0">
          <stop offset="0" stop-color="#0a0f3a"/>
          <stop offset="0.55" stop-color="#0a3fd0"/>
          <stop offset="1" stop-color="#0a1a6a"/>
        </linearGradient>
      </defs>
      <polygon points="0,0 400,0 394,23 0,23" fill="url(#bandBlue)"/>
      <polygon points="408,0 615,0 615,23 402,23" fill="#cc0000"/>
    </svg>
  </section>

  <section class="card card-back" aria-label="Business card back">
    <div class="back-brand">
      <span class="brand-mark" aria-hidden="true"></span>
      <div class="brand-name">Lakeshore Claims Adjusters</div>
    </div>
    <div class="back-rule"></div>
    <div class="back-url">www.LakeshoreClaimsAdjusters.com</div>
  </section>

</main>
</body>
</html>
```